Responsive web design for leading product search engine

Findnearby is the leading product search engine in Australia and is soon to expand into Asia. We need a lightweight responsive homepage designed for our 3 regional domains. Our domains are Findnearby.com, Findnearby.com.au and Findnearby.asia. We need 3 versions of the same page to appeal to each region. The page and images used need to use a responsive html 5 based web page. The images used in the design need to be responsive and include CSS3 style elements.

For inspiration I would divert you to www.brovanta.com and www.pelmiqo.com.au and I have attached a mockup of what I think it could look like.
Updates

Target Market(s)

Target market is female shoppers 16-40 years old

Industry/Entity Type

Retail

Coding

Coded - Design and coding required

Number of Pages Required

3 page

Colors
33b8a4

Requirements
Must have
• Different image for each of the 3 duplicate pages. 1 for each region Australia (.com.au) Asia (.asia) US (.com). These images must be licensed for public use.

```html
<!DOCTYPE html>
<html lang="en">
<head>
<meta charset="utf-8">
<title>Findnearby – Product search</title>
<link href="https://fonts.googleapis.com/css2?family=Roboto:wght@300;400;500;700&display=swap" rel="stylesheet">
<style>
:root{
  --teal:#33b8a4;
  --teal-dark:#2aa692;
  --ink:#3a3a3a;
  --muted:#8a8a8a;
  --light:#f2f2f2;
  --white:#ffffff;
  --hero-a:#c9cdd0;
  --hero-b:#7f8891;
}
*{box-sizing:border-box;margin:0;padding:0}
html,body{width:713px;height:1200px;overflow:hidden}
body{font-family:'Roboto',sans-serif;color:var(--ink);background:var(--white);position:relative}

.site-header{height:71px;display:flex;align-items:center;justify-content:space-between;padding:0 28px 0 24px;background:var(--white)}
.brand{display:flex;align-items:center;gap:8px;color:var(--teal);font-size:25px;font-weight:500;text-decoration:none}
.brand-dot{width:30px;height:30px;border-radius:50%;border:3px solid var(--teal)}
.main-nav{display:flex;align-items:center;gap:18px;font-size:12px}
.main-nav a{color:var(--ink);text-decoration:none}
.btn-outline{border:1.5px solid var(--teal);color:var(--teal)!important;padding:6px 12px;border-radius:2px}
.btn-solid{background:var(--teal);color:var(--white)!important;padding:7px 18px;border-radius:2px}

.hero{position:relative;height:434px;overflow:hidden}
.hero-photo{position:absolute;inset:0;background:linear-gradient(180deg,var(--hero-a) 0%,#a9afb4 45%,var(--hero-b) 100%)}
.search-bar{position:absolute;top:245px;left:121px;display:flex;gap:8px}
.field{height:40px;background:var(--white);display:flex;align-items:center;gap:8px;padding:0 12px;font-size:11px;color:var(--muted)}
.field-query{width:172px}
.field-location{width:172px}
.search-btn{width:112px;height:40px;background:var(--teal);color:var(--white);border:0;font-family:inherit;font-size:13px;font-weight:500;letter-spacing:2px}
.hero-title{position:absolute;top:345px;left:0;right:0;text-align:center;color:var(--white);font-weight:300;font-size:26px;line-height:1.2}

.discover{height:341px;background:var(--light);position:relative}
.discover-icon{position:absolute;left:76px;top:58px;width:50px;height:50px;border-radius:50%;background:var(--teal);display:flex;align-items:center;justify-content:center}
.discover h2{position:absolute;left:76px;top:128px;width:250px;font-weight:400;font-size:21px;line-height:1.3}
.discover p{position:absolute;left:76px;top:200px;width:240px;font-size:12px;line-height:1.6;color:var(--muted)}
.devices{position:absolute;left:345px;top:30px;width:365px;height:278px;border-radius:14px;background:linear-gradient(135deg,#2f2f2f,#555 60%,#e5e5e5)}

.partners{height:105px;display:flex;align-items:center;justify-content:space-around;padding:0 18px;font-size:17px;font-weight:500;color:#555}

.site-footer{position:absolute;top:950px;left:0;width:713px;height:250px;background:var(--teal);color:var(--white);text-align:center}
.footer-brand{display:inline-flex;align-items:center;gap:8px;margin-top:24px;font-size:23px;font-weight:500}
.footer-brand .brand-dot{border-color:var(--white);width:26px;height:26px}
.footer-links{margin-top:14px;display:flex;justify-content:center;gap:18px;font-size:10px}
.store-badges{margin-top:18px;display:flex;justify-content:center;gap:10px}
.store-badge{width:92px;height:28px;background:#1c1c1c;border-radius:4px}
.social{margin-top:18px;display:flex;justify-content:center;gap:10px}
.social span{width:20px;height:20px;border-radius:50%;background:rgba(255,255,255,.35)}
.copyright{margin-top:24px;font-size:9px;opacity:.85}
</style>
</head>
<body>
<header class="site-header">
  <a class="brand" href="#"><span class="brand-dot"></span>Findnearby</a>
  <nav class="main-nav">
    <a href="#">Home</a>
    <a href="#">Add New Business</a>
    <a href="#" class="btn-outline">Register</a>
    <a href="#" class="btn-solid">Login</a>
  </nav>
</header>

<section class="hero">
  <div class="hero-photo" role="img" aria-label="Blurred shoppers walking through a bright shopping mall"></div>
  <form class="search-bar">
    <div class="field field-query">
      <svg width="12" height="12" viewBox="0 0 12 12"><circle cx="5" cy="5" r="3.5" fill="none" stroke="#999" stroke-width="1.4"/><line x1="7.6" y1="7.6" x2="11" y2="11" stroke="#999" stroke-width="1.4"/></svg>
      Search Business or Product
    </div>
    <div class="field field-location">
      <svg width="10" height="13" viewBox="0 0 10 13"><path d="M5 12.5C5 12.5 1 7.6 1 4.8a4 4 0 0 1 8 0C9 7.6 5 12.5 5 12.5z" fill="#999"/><circle cx="5" cy="4.8" r="1.5" fill="#fff"/></svg>
      Current Location
    </div>
    <button class="search-btn" type="button">SEARCH</button>
  </form>
  <h1 class="hero-title">Search millions of products<br>on sale at nearby stores</h1>
</section>

<section class="discover">
  <div class="discover-icon">
    <svg width="24" height="22" viewBox="0 0 24 22"><path d="M8 2 L3 5 L1 10 L5 11 L5 21 L19 21 L19 11 L23 10 L21 5 L16 2 Q12 6 8 2z" fill="none" stroke="#fff" stroke-width="1.8" stroke-linejoin="round"/></svg>
  </div>
  <h2>Discover the best products while you shop</h2>
  <p>Search every product in every store and you'll never miss out on the latest trends on sale in your area.</p>
  <div class="devices" role="img" aria-label="Tablet and phone showing the Findnearby product pages"></div>
</section>

<section class="partners">
  <span>Vellamo</span>
  <span>Corvex</span>
  <span>Tindle</span>
  <span>Orbisell</span>
  <span>Paxwell</span>
</section>

<footer class="site-footer">
  <div class="footer-brand"><span class="brand-dot"></span>Findnearby</div>
  <nav class="footer-links">
    <span>Findnearby for business</span>
    <span>Why Findnearby?</span>
    <span>FAQ</span>
    <span>Contact us</span>
    <span>Blog</span>
    <span>Privacy policy</span>
  </nav>
  <div class="store-badges">
    <span class="store-badge"></span>
    <span class="store-badge"></span>
  </div>
  <div class="social"><span></span><span></span><span></span><span></span><span></span></div>
  <p class="copyright">Copyright © 2015 All Rights Reserved</p>
</footer>
</body>
</html>
```